Boutique custom software development company needs new business card

Our nearly 20 year old custom software development company would like to better include the fact that we are now providing Bitcoin services. These new services are B2B include education (how to acquire and securely hold Bitcoin) and integrating Bitcoin payments into existing ecommerce sites or other existing systems. Please keep the card clean and simple. Attached is our current design and some other files. vextorial.com

Target Market(s)

businesses owners interested in long term relationship

Industry/Entity Type

Custom software development and Bitcoin

Contact Information for Business Card

Dale Parker, dale@vextorial.com, vextorial.com, (888) 555-VXTRL

Font styles to use
Other font styles liked:
• monospace

Requirements
Must have
• double-sided
Nice to have
• clean and simple
Should not have
• physical address

```html
<!DOCTYPE html>
<html lang="en">
<head>
<meta charset="utf-8">
<title>Vextorial Business Card</title>
<link href="https://fonts.googleapis.com/css2?family=Montserrat:wght@700;800&family=Poppins:wght@400;600&display=swap" rel="stylesheet">
<style>
  :root {
    --stage: #1b1b1b;
    --card-white: #ffffff;
    --brand-orange: #f17b22;
    --brand-blue: #3c6fb9;
    --ink: #3a3a3a;
    --divider: #c9d6ea;
    --deboss: #9c4d12;
  }
  * { margin: 0; padding: 0; box-sizing: border-box; }
  html, body { width: 1075px; height: 1200px; overflow: hidden; }
  body { background: var(--stage); position: relative; font-family: "Poppins", sans-serif; }

  .card {
    position: absolute;
    border-radius: 27px;
    box-shadow: 4px 5px 4px rgba(0,0,0,0.75);
  }
  .card--front { left: 209px; top: 188px; width: 659px; height: 393px; background: var(--card-white); }
  .card--back  { left: 206px; top: 637px; width: 663px; height: 393px; background: var(--brand-orange); }

  .brand { position: absolute; left: 48px; top: 158px; width: 250px; text-align: center; }
  .brand__name {
    font-family: "Montserrat", sans-serif; font-weight: 800;
    font-size: 40px; letter-spacing: 0.5px; line-height: 1; color: var(--brand-blue);
  }
  .brand__tagline {
    margin-top: 11px; font-size: 16px; letter-spacing: -0.5px; color: var(--brand-blue); white-space: nowrap;
  }

  .divider { position: absolute; left: 329px; top: 118px; width: 1px; height: 157px; background: var(--divider); }

  .person {
    position: absolute; left: 364px; top: 119px;
    font-family: "Montserrat", sans-serif; font-weight: 800; font-size: 27px; letter-spacing: 0.2px;
  }
  .person__first { color: var(--brand-orange); }
  .person__last { color: var(--brand-blue); }

  .contacts { position: absolute; left: 364px; top: 184px; list-style: none; }
  .contacts__item {
    display: flex; align-items: center; gap: 9px; height: 29.5px;
    font-size: 20px; color: var(--ink); white-space: nowrap;
  }
  .contacts__icon {
    width: 25px; height: 25px; border-radius: 3px; background: var(--brand-orange);
    display: flex; align-items: center; justify-content: center; flex: none;
  }
  .contacts__highlight { color: var(--brand-blue); }

  .back-name {
    position: absolute; left: 0; right: 0; top: 163px; text-align: center;
    font-family: "Montserrat", sans-serif; font-weight: 800; font-size: 64px; line-height: 1;
    color: var(--deboss);
  }
</style>
</head>
<body>
  <section class="card card--front" aria-label="Card front">
    <div class="brand">
      <div class="brand__name">VEXTORIAL</div>
      <div class="brand__tagline">developer of custom applications</div>
    </div>
    <div class="divider"></div>
    <div class="person"><span class="person__first">DALE</span> <span class="person__last">PARKER</span></div>
    <ul class="contacts">
      <li class="contacts__item">
        <span class="contacts__icon">
          <svg width="16" height="16" viewBox="0 0 24 24"><path d="M6.6 10.8a15 15 0 0 0 6.6 6.6l2.2-2.2c.3-.3.7-.4 1-.2 1.1.4 2.3.6 3.6.6.6 0 1 .4 1 1V20c0 .6-.4 1-1 1A17 17 0 0 1 3 4c0-.6.4-1 1-1h3.5c.6 0 1 .4 1 1 0 1.3.2 2.5.6 3.6.1.3 0 .7-.2 1z" fill="none" stroke="#fff" stroke-width="1.8"/></svg>
        </span>(888) 555-VXTRL
      </li>
      <li class="contacts__item">
        <span class="contacts__icon">
          <svg width="17" height="13" viewBox="0 0 17 13"><rect x="1" y="1" width="15" height="11" fill="none" stroke="#fff" stroke-width="1.5"/><path d="M1 1l7.5 6L16 1M1 12l5.5-5M16 12l-5.5-5" fill="none" stroke="#fff" stroke-width="1.3"/></svg>
        </span>dale@vextorial.com
      </li>
      <li class="contacts__item">
        <span class="contacts__icon">
          <svg width="16" height="16" viewBox="0 0 16 16" fill="none" stroke="#fff" stroke-width="1.2"><circle cx="8" cy="8" r="6.5"/><ellipse cx="8" cy="8" rx="3" ry="6.5"/><path d="M1.5 8h13M2.5 4.8h11M2.5 11.2h11"/></svg>
        </span>www.<span class="contacts__highlight">vextorial</span>.com
      </li>
    </ul>
  </section>

  <section class="card card--back" aria-label="Card back">
    <div class="back-name">VEXTORIAL</div>
  </section>
</body>
</html>
```